Brindle Yard Care. The best in the biz

I run a lawn care service that offers full service mowing. 100% satisfaction guarantee. Fast, Friendly, quality service "I am your lawns best friend" I cut residential lawns. I offer a mow package that includes trimming, edging and clean up. Prices very from 20 dollars to 75. I want my logo to stand out. Free estimates

Target Market(s)

Home owners

Industry/Entity Type

Landscaping

Contact Information for Business Card

555-812-4473 tomvale48@quillmail.net Derek. Brindle Yard care

Colors
f37122
9bcb3c
cadf82

Requirements
Must have
• Company name.
• Phone number
• Email
• My services
• images
Nice to have
• A sun that is growing grass.
Should not have
• Incorrect information

```html
<!DOCTYPE html>
<html lang="en">
<head>
<meta charset="utf-8">
<title>Brindle Yard Care – Business Card</title>
<link href="https://fonts.googleapis.com/css2?family=Source+Sans+3:ital,wght@0,400;0,600;0,700;1,400&display=swap" rel="stylesheet">
<style>
  :root {
    --backdrop: #3b3634;
    --card: #141414;
    --brand-green: #2f9e3e;
    --band-green: #1fa53a;
    --accent-yellow: #e4e21b;
    --sun-orange: #f37122;
    --text-light: #f2f2f2;
    --divider: #6a6a6a;
  }
  * { box-sizing: border-box; margin: 0; padding: 0; }
  html, body {
    width: 1200px; height: 814px; overflow: hidden;
    background: var(--backdrop);
    font-family: "Source Sans 3", "Helvetica Neue", Arial, sans-serif;
  }
  .canvas { position: relative; width: 1200px; height: 814px; }
  .card {
    position: absolute; top: 252px;
    width: 540px; height: 310px;
    background: var(--card);
    border-radius: 4px;
    overflow: hidden;
    box-shadow: 0 6px 18px rgba(0,0,0,.35);
  }
  .card--front { left: 45px; }
  .card--back { left: 615px; }

  /* brand lockup */
  .brand { position: absolute; display: flex; align-items: center; gap: 9px; }
  .brand__sun { border-radius: 50%; background: var(--sun-orange); flex: none; }
  .brand__name { color: var(--brand-green); font-weight: 700; line-height: 1; white-space: nowrap; }

  .card--front .brand { left: 30px; top: 96px; }
  .card--front .brand__sun { width: 34px; height: 34px; }
  .card--front .brand__name { font-size: 23px; }

  .tagline {
    position: absolute; left: 32px; top: 146px;
    color: var(--text-light); font-style: italic; font-size: 15px; letter-spacing: .4px;
    white-space: nowrap;
  }

  .divider {
    position: absolute; left: 300px; top: 36px;
    width: 1px; height: 132px; background: var(--divider);
  }

  .contact { position: absolute; left: 316px; top: 40px; color: var(--text-light); font-size: 13px; line-height: 1.45; white-space: nowrap; }
  .contact__name { color: var(--band-green); font-size: 17px; font-weight: 600; line-height: 1.2; }
  .contact__title { color: var(--accent-yellow); font-size: 13px; margin-bottom: 6px; }
  .contact__row { display: flex; align-items: center; gap: 7px; }
  .contact__row svg { flex: none; }

  .service-band {
    position: absolute; left: 0; right: 0; bottom: 0; height: 92px;
    background: var(--band-green);
    border-top: 3px solid var(--accent-yellow);
  }
  .services {
    position: absolute; left: 0; right: 0; top: 18px; text-align: center;
    color: var(--accent-yellow); font-size: 17px; font-weight: 600; letter-spacing: .3px;
  }
  .band-stripe {
    position: absolute; left: 0; right: 0; top: 50px; height: 2px; background: rgba(0,0,0,.35);
  }

  .card--back .brand { left: 120px; top: 128px; }
  .card--back .brand__sun { width: 52px; height: 52px; }
  .card--back .brand__name { font-size: 40px; }
</style>
</head>
<body>
<main class="canvas">

  <section class="card card--front" aria-label="Business card front">
    <div class="brand">
      <span class="brand__sun" aria-hidden="true"></span>
      <span class="brand__name">Brindle Yard Care</span>
    </div>
    <p class="tagline">A sun that is growing grass.</p>

    <div class="divider"></div>

    <div class="contact">
      <p class="contact__name">Paul Marsh</p>
      <p class="contact__title">CEO/Founder</p>
      <p>Derek, Brindle Yard care</p>
      <p class="contact__row">
        <svg width="11" height="11" viewBox="0 0 24 24" aria-hidden="true"><path fill="#1fa53a" d="M6.6 10.8a15.1 15.1 0 0 0 6.6 6.6l2.2-2.2c.3-.3.7-.4 1-.2 1.1.4 2.3.6 3.6.6.6 0 1 .4 1 1V20c0 .6-.4 1-1 1A17 17 0 0 1 3 4c0-.6.4-1 1-1h3.5c.6 0 1 .4 1 1 0 1.3.2 2.5.6 3.6.1.3 0 .7-.2 1z"/></svg>
        555-812-4473
      </p>
      <p class="contact__row">
        <svg width="11" height="9" viewBox="0 0 24 18" aria-hidden="true"><rect width="24" height="18" rx="2" fill="#1fa53a"/><path d="M2 2l10 8 10-8" fill="none" stroke="#141414" stroke-width="2"/></svg>
        tomvale48@quillmail.net
      </p>
    </div>

    <div class="service-band">
      <p class="services">Trimming • edging • clean up</p>
      <div class="band-stripe"></div>
    </div>
  </section>

  <section class="card card--back" aria-label="Business card back">
    <div class="brand">
      <span class="brand__sun" aria-hidden="true"></span>
      <span class="brand__name">Brindle Yard Care</span>
    </div>
  </section>

</main>
</body>
</html>
```